Briloran Clear Springs needs a new business card design (we produce and sell pure bottled water)

We need a clean modern design for our new business cards, We have an existing logo which ultimately cannot be changed, however it could be slighty improved and the colours adjusted. We have this existing logo on all of our bottles, vehicles etc.

Our company slogan is "Clear right to the final sip".
Along with our relevant company information
(Address, phone, website email etc) we will only be using names and not putting position titles for flexibilty.

We are looking for a clean, minimalist modern design.

You can view our website (if need of an update also!) to see our business.

Industry/Entity Type

Business

Contact Information for Business Card

Staff Name : XXXXXX XXXXXX
Address : 9/41 Tavenor St
Halden Rise QLD 4172
Staff Mobile Number : 04XX XXX XXX
Office Phone Number : 07 3918 2457
Staff Email Address : XXXX@brilorancleargo.com.au
Website : www.brilorancleargo.com.au

Font styles to use
Sans Serif

Colors
cee9f5
33a6d7
0492cd
0455a3
3276b5
85abd2
cedeed

Requirements
Must have
• The ability to edit and change the staff members details as we will need to edit for each respective staff member (7 in total)

```html
<!DOCTYPE html>
<html lang="en">
<head>
<meta charset="utf-8">
<title>Briloran Clear Springs – Business Card</title>
<link href="https://fonts.googleapis.com/css2?family=Arimo:wght@700&family=Open+Sans:wght@400;600;700&display=swap" rel="stylesheet">
<style>
  :root {
    --backdrop-top: #959595;
    --backdrop-bottom: #6c6c6c;
    --card-front: #f2f2f2;
    --card-back: #161616;
    --ink: #111111;
    --slogan: #ffffff;
    --slogan-shadow: #555555;
  }
  * { margin: 0; padding: 0; box-sizing: border-box; }
  html, body { width: 1200px; height: 900px; overflow: hidden; }
  body {
    position: relative;
    background: linear-gradient(to bottom, var(--backdrop-top), var(--backdrop-bottom));
    font-family: "Open Sans", Arial, sans-serif;
    color: var(--ink);
  }
  .card {
    position: absolute;
    top: 184px;
    height: 490px;
    border-radius: 12px;
    overflow: hidden;
  }
  .card--front {
    left: 299px;
    width: 301px;
    background: var(--card-front);
    text-align: center;
  }
  .card--back {
    left: 645px;
    width: 304px;
    background: var(--card-back);
  }
  .brand {
    position: absolute;
    left: 0; right: 0;
    top: 50px;
    font-weight: 700;
    color: var(--ink);
    line-height: 1;
  }
  .brand__mark {
    display: block;
    width: 64px; height: 64px;
    margin: 0 auto 22px;
    border-radius: 50%;
    background: var(--ink);
  }
  .brand__name { display: block; font-size: 32px; letter-spacing: 0.5px; }
  .brand__sub { display: block; font-size: 19px; margin-top: 6px; letter-spacing: 0.6px; }
  .staff-name {
    position: absolute;
    left: 0; right: 0;
    top: 274px;
    font-size: 16.5px;
    font-weight: 600;
  }
  .contact {
    position: absolute;
    left: 0; right: 0;
    font-size: 13.2px;
    line-height: 18px;
  }
  .contact--address { top: 319px; }
  .contact--reach { top: 367px; }
  .slogan {
    position: absolute;
    inset: 0;
    text-align: center;
    font-family: "Arimo", Arial, sans-serif;
    font-weight: 700;
    color: var(--slogan);
    line-height: 1;
    text-shadow: 3px 4px 2px var(--slogan-shadow);
  }
  .slogan__line {
    position: absolute;
    left: 0; right: 0;
    font-size: 53px;
    letter-spacing: 3px;
  }
  .slogan__line--big { font-size: 70px; letter-spacing: 3px; }
</style>
</head>
<body>
  <section class="card card--front">
    <div class="brand">
      <span class="brand__mark"></span>
      <span class="brand__name">BRILORAN</span>
      <span class="brand__sub">CLEAR SPRINGS</span>
    </div>
    <p class="staff-name">Darrell Okonby</p>
    <p class="contact contact--address">9/41 Tavenor St<br>Halden Rise QLD 4172</p>
    <p class="contact contact--reach">0400 765 218<br>07 3918 2457<br>info@brilorancleargo.com.au<br>www.brilorancleargo.com.au</p>
  </section>

  <section class="card card--back">
    <h2 class="slogan">
      <span class="slogan__line" style="top:58px">CLEAR</span>
      <span class="slogan__line" style="top:118px">RIGHT</span>
      <span class="slogan__line" style="top:177px">TO</span>
      <span class="slogan__line slogan__line--big" style="top:244px">THE</span>
      <span class="slogan__line" style="top:323px">FINAL</span>
      <span class="slogan__line" style="top:384px">SIP</span>
    </h2>
  </section>
</body>
</html>
```